Specialised investor in e-mobility and energy wants business card design

We need a business card design that fits our existing corporate design. <The look and feel must be 'sharp'/'clean', dynamic, communicate momentum, professionalism etc (as one would imagine from a firm in the financial sector). We like the idea of a reverse-side of the card that includes the logo, and the name and contact details on the other. We expect the deliverable to be whatever format might be required to be able to get cards printed directly by a service such as kelmo press. Our website is www.zub.capital

```html
<!DOCTYPE html>
<html lang="en">
<head>
<meta charset="utf-8">
<title>Zub Capital – Business Card</title>
<link rel="stylesheet" href="https://fonts.googleapis.com/css2?family=Montserrat:wght@400;500;800&display=swap">
<style>
  :root {
    --stage: #d3d6d5;
    --paper: #f3f3f1;
    --green-dark: #1c3a12;
    --green-light: #67a52f;
    --ink: #333a36;
  }
  * { margin: 0; padding: 0; box-sizing: border-box; }
  html, body {
    width: 1200px; height: 905px; overflow: hidden;
    background: var(--stage);
    font-family: "Montserrat", sans-serif;
  }
  .sheet {
    width: 1200px; height: 905px;
    display: flex; align-items: center; justify-content: center; gap: 50px;
  }
  .card {
    position: relative;
    width: 540px; height: 309px;
    background: var(--paper);
    box-shadow: 0 10px 30px rgba(0,0,0,.15);
    overflow: hidden;
  }
  .card--front { border-bottom: 3px solid var(--green-light); }
  .brand {
    font-weight: 500;
    color: var(--green-dark);
    letter-spacing: .5px;
    white-space: nowrap;
  }
  .card--front .brand {
    position: absolute; top: 42px; left: 150px;
    font-size: 46px;
  }
  .card--back .brand {
    position: absolute; top: 50%; left: 50%;
    transform: translate(-50%, -50%);
    font-size: 58px;
  }
  .contact {
    position: absolute; left: 40px; top: 138px;
    list-style: none;
    font-size: 15px; line-height: 23px; color: var(--ink);
  }
  .contact .address { margin-bottom: 6px; padding-left: 22px; }
  .contact li { display: flex; align-items: center; gap: 8px; }
  .contact svg { width: 14px; height: 14px; fill: var(--green-light); flex: none; }
  .person {
    position: absolute; right: 40px; bottom: 40px; text-align: right;
  }
  .person__name {
    font-weight: 800; font-size: 21px; letter-spacing: 1px;
    color: var(--green-dark);
  }
  .person__name span { color: var(--green-light); }
  .person__role { font-size: 15px; color: var(--ink); margin-top: 2px; }
</style>
</head>
<body>
<main class="sheet">
  <section class="card card--front" aria-label="Business card front">
    <div class="brand">Zub Capital</div>
    <ul class="contact">
      <li class="address">5678 Harbor Lane<br>Region Name CD 2916</li>
      <li><svg viewBox="0 0 16 16" aria-hidden="true"><path d="M3.6 1.5l2.3 2.3-1.3 2a9 9 0 0 0 5.6 5.6l2-1.3 2.3 2.3-1.6 2.1C7.7 14.3 1.7 8.3 1.5 3.1z"/></svg>123-480-2291</li>
      <li><svg viewBox="0 0 16 16" aria-hidden="true"><path d="M1 3h14v10H1z M1 3l7 6 7-6" fill="none" stroke="#67a52f" stroke-width="1.6"/></svg>info@zub.capital</li>
      <li><svg viewBox="0 0 16 16" aria-hidden="true"><circle cx="8" cy="8" r="6.5" fill="none" stroke="#67a52f" stroke-width="1.5"/><path d="M1.5 8h13M8 1.5c-3 3.5-3 9.5 0 13M8 1.5c3 3.5 3 9.5 0 13" fill="none" stroke="#67a52f" stroke-width="1.2"/></svg>www.zub.capital</li>
    </ul>
    <div class="person">
      <div class="person__name">MAREK <span>OLSEN</span></div>
      <div class="person__role">Director/Founder</div>
    </div>
  </section>
  <section class="card card--back" aria-label="Business card back">
    <div class="brand">Zub Capital</div>
  </section>
</main>
</body>
</html>
```